Delphine's Stone Hearth Trattoria Pitch Deck

Clean and Minimalist Layout: Use a clean and uncluttered layout with ample white space to enhance readability and focus on the key content.

Color Palette: Choose a color scheme that aligns with your brand identity. Black and White. Opt for a combination of complementary colors to create a visually appealing and cohesive look throughout the presentation.

Typography: Select modern and legible fonts for headings and body text. Consider using a combination of serif and sans-serif fonts to create contrast and hierarchy.

High-Quality Images: Incorporate high-resolution images that visually represent your pizzeria, food offerings, and brand. Ensure the images are clear, well-lit, and of professional quality.

Graphs and Charts: Utilize visually appealing graphs and charts to present financial projections, market data, and growth metrics. Choose appropriate chart types, such as bar graphs or line charts, to effectively communicate data.

Iconography: Include relevant icons and symbols to enhance visual interest and provide quick visual cues. Use them to represent different sections, services, or key points in your presentation.

Slide Transitions and Animations: Use subtle slide transitions and animations to add a touch of interactivity and engage your audience. However, avoid overusing flashy animations that may distract from the content.

Consistent Branding: Ensure that your pitch deck maintains consistent branding elements throughout, such as your logo, color scheme, and typography. This helps to reinforce your brand identity and create a cohesive presentation.

Remember, the goal is to create a visually appealing and professional pitch deck that effectively communicates your key messages. Use visuals, graphs, and design elements strategically to enhance understanding and engagement with your audience.

Target Market(s)

Investors

Industry/Entity Type

Food Industry

Font styles to use
Serif

Colors

Designer to choose only greyscale colors for use in the design.

Requirements
Must have
• Modern and Professional Look: Opt for a modern design that reflects the professional nature of your business. Use clean lines, contemporary fonts, and a visually appealing color scheme to create a polished and professional appearance. Consistent Branding: Incorporate your pizzeria's branding elements such as the logo, colors, and typography throughout the pitch deck. Consistency in branding helps to establish a cohesive and memorable visual identity. Visual Hierarchy: Use visual hierarchy to guide the viewer's attention and emphasize important information. Utilize font sizes, colors, and formatting techniques such as bold and italics to differentiate headings, subheadings, and body text. Engaging Visuals: Incorporate relevant and eye-catching visuals such as high-quality images, graphics, and icons. Visuals should support your content and help communicate your message effectively. Well-Structured Layout: Organize your content into sections and use clear headings and subheadings to create a logical flow. Ensure that each slide has enough white space for readability and avoid cluttered designs. Legible Fonts: Choose fonts that are easy to read on both computer screens and projection screens. Stick to a maximum of two font styles to maintain a clean and professional look. Charts and Graphs: When presenting data or statistics, use charts, graphs, and infographics to present information visually. This makes complex information more digestible and visually appealing. Slide Transitions and Animations: Use slide transitions and subtle animations to enhance the visual experience. However, avoid excessive animations that can distract from your content. Balance of Text and Visuals: Strike a balance between text and visuals. Avoid overcrowding slides with excessive text and focus on presenting key points in a concise and visually appealing manner. Relevance to Content: Ensure that the design elements align with and enhance the content of your pitch deck. Avoid using decorative elements that do not serve a purpose or distract from the main message. Remember, the design should complement and support your content rather than overpowering it. A well-designed pitch deck will capture attention, convey professionalism, and enhance the overall impact of your presentation.

```html
<!DOCTYPE html>
<html lang="en">
<head>
<meta charset="utf-8">
<title>Delphine's Stone Hearth Trattoria – Pitch Deck</title>
<link href="https://fonts.googleapis.com/css2?family=Italianno&family=Nunito+Sans:wght@400;600&family=Oswald:wght@500&family=Cormorant+Garamond:wght@500&display=swap" rel="stylesheet">
<style>
:root{
  --ink:#111;
  --body:#333;
  --muted:#555;
  --paper:#fff;
  --canvas:#fff;
  --gold:#e0a500;
  --shadow:rgba(0,0,0,.16);
}
*{margin:0;padding:0;box-sizing:border-box}
html,body{width:1200px;height:1111px;overflow:hidden;background:var(--canvas)}
body{position:relative;font-family:"Nunito Sans",sans-serif;color:var(--body)}
.slide{position:absolute;width:509px;height:286px;background:var(--paper);box-shadow:0 4px 18px var(--shadow);overflow:hidden}
.s1{left:70px;top:77px}.s2{left:619px;top:77px}
.s3{left:70px;top:408px}.s4{left:619px;top:408px}
.s5{left:70px;top:739px}.s6{left:619px;top:739px}
.abs{position:absolute}
.storefront{position:absolute;inset:0;background:linear-gradient(160deg,#f4f4f2 0%,#fafaf9 40%,#e9ebea 75%,#f3f3f1 100%)}
.brand{position:absolute;font-family:"Nunito Sans",sans-serif;font-weight:600;color:var(--ink);white-space:nowrap;transform:translateX(-50%);text-align:center}
.brand-sm{font-size:13px}
.script{font-family:"Italianno",cursive;color:var(--ink);font-weight:400;line-height:1}
.title{font-size:34px}
.sub{font-size:21px}
.rule{position:absolute;height:2px;background:var(--ink)}
.text{font-size:7.4px;line-height:12px;color:var(--body)}
.bullets{list-style:none}
.bullets li{position:relative;padding-left:11px;text-align:justify}
.bullets li::before{content:"";position:absolute;left:1px;top:4.5px;width:3px;height:3px;border-radius:50%;background:var(--ink)}
.page{position:absolute;right:0;bottom:0;width:39px;height:18px;background:var(--ink);color:#fff;font-family:"Cormorant Garamond",serif;font-size:7px;display:flex;align-items:center;justify-content:center}
.photo{position:absolute}
.round{border-radius:50%}
.portrait{position:absolute;width:70px;height:70px;border-radius:50%;background:var(--gold);transform:translate(-50%,-50%)}
.portrait .face{position:absolute;left:12px;top:12px;width:46px;height:46px;border-radius:50%;background:linear-gradient(#9a7b68,#d9d4cf)}
.person{position:absolute;transform:translateX(-50%);text-align:center;white-space:nowrap}
.name{font-family:"Oswald",sans-serif;font-weight:500;font-size:11px;color:var(--ink);letter-spacing:.2px}
.role{font-size:7.6px;color:var(--muted);margin-top:2px}
.dash{width:24px;height:1.5px;background:var(--ink);margin:6px auto 5px}
.email{font-size:7.8px;color:var(--ink);font-weight:600}
.col{position:absolute;width:117px;transform:translateX(-50%);text-align:center}
.col .sub{font-size:20px;line-height:21px}
.col .mini{width:24px;height:1px;background:var(--ink);margin:4px auto 6px}
.col .text{text-align:justify;text-align-last:center}
.person.left{transform:none;text-align:left}
.person.left .dash{margin:5px 0 4px}
</style>
</head>
<body>

<!-- Cover -->
<section class="slide s1">
  <div class="storefront" role="img" aria-label="Faded photo of the trattoria storefront and signage"></div>
  <div class="brand" style="left:254px;top:72px;font-size:38px">Delphine's</div>
  <div class="brand" style="left:254px;top:118px;font-size:8px;letter-spacing:3px">STONE HEARTH TRATTORIA</div>
  <div class="portrait" style="left:140px;top:181px"><div class="face" role="img" aria-label="Portrait of Marco Bellanti"></div></div>
  <div class="portrait" style="left:363px;top:181px"><div class="face" role="img" aria-label="Portrait of Owen Hartley"></div></div>
  <div class="person" style="left:140px;top:224px"><div class="name">MARCO BELLANTI</div><div class="role">Owner &amp; CEO</div><div class="dash"></div><div class="email">marco@delphinestrattoria.com</div></div>
  <div class="person" style="left:363px;top:224px"><div class="name">OWEN HARTLEY</div><div class="role">Owner, Silent Partner</div><div class="dash"></div><div class="email">owen@delphinestrattoria.com</div></div>
</section>

<!-- Introduction -->
<section class="slide s2">
  <h2 class="script title abs" style="left:23px;top:18px;font-size:40px">Introduction</h2>
  <div class="rule" style="left:26px;top:62px;width:123px"></div>
  <h3 class="script sub abs" style="left:24px;top:76px">Brief Introduction to the Trattoria</h3>
  <ul class="bullets text abs" style="left:25px;top:101px;width:241px">
    <li>Delphine's Stone Hearth Trattoria is a quality casual restaurant offering freshly cooked, delicious pizzas made with carefully crafted homemade sauce and dough. We prioritize customer satisfaction and provide lightning-quick food times, making us a top choice for takeout and delivery.</li>
  </ul>
  <h3 class="script sub abs" style="left:23px;top:170px">Vision and Mission Statement:</h3>
  <ul class="bullets text abs" style="left:25px;top:195px;width:241px">
    <li>Our vision is to become the go-to destination for exceptional pizza experiences, known for our quality ingredients and outstanding service. Our mission is to delight customers with every bite and create memorable moments through our delicious pizzas.</li>
  </ul>
  <div class="photo round" style="left:308px;top:64px;width:186px;height:186px;background:radial-gradient(circle at 45% 65%,#e2b36d,#c98a3e 45%,#b49a7c 75%,#8b6f55)" role="img" aria-label="Chef seasoning a freshly baked pizza"></div>
  <div class="brand brand-sm" style="left:467px;top:17px">Delphine's</div>
  <div class="page">Page 02</div>
</section>

<!-- Market Opportunity -->
<section class="slide s3">
  <h2 class="script title abs" style="left:0;width:509px;text-align:center;top:14px;font-size:40px">The Market Opportunity</h2>
  <div class="rule" style="left:192px;top:59px;width:125px"></div>
  <div class="brand brand-sm" style="left:467px;top:17px">Delphine's</div>
  <div class="col" style="left:96px;top:96px">
    <h3 class="script sub">Overview of the Pizza Industry:</h3><div class="mini"></div>
    <p class="text">The pizza industry is a thriving and highly popular segment of the food service market. With a diverse range of customers and a growing demand for convenient dining options, the pizza industry presents significant growth opportunities.</p>
  </div>
  <div class="col" style="left:259px;top:96px">
    <h3 class="script sub">Market Size and Growth Potential:</h3><div class="mini"></div>
    <p class="text">The pizza industry is a thriving and highly popular segment of the food service market. With a diverse range of customers and a growing demand for convenient dining options, the pizza industry presents significant growth opportunities.</p>
  </div>
  <div class="col" style="left:421px;top:96px;height:170px;overflow:hidden">
    <h3 class="script sub">Target Audience and Customer Demographics:</h3><div class="mini"></div>
    <p class="text">Our target audience encompasses a wide range of individuals from 18 to 80 years old, both male and female, with a focus on the middle-class demographic. By offering a menu that caters to diverse tastes and preferences, we can attract a broad customer base.</p>
  </div>
  <div class="page">Page 03</div>
</section>

<!-- Unique Selling Proposition -->
<section class="slide s4">
  <h2 class="script title abs" style="left:0;width:509px;text-align:center;top:4px;font-size:38px">Unique Selling Proposition</h2>
  <div class="rule" style="left:210px;top:40px;width:70px;height:1.5px"></div>
  <div class="brand brand-sm" style="left:467px;top:17px">Delphine's</div>
  <div class="photo" style="left:50px;top:56px;width:154px;height:101px;background:linear-gradient(180deg,#3a2a20 0%,#b8561f 30%,#d98a3c 60%,#6e6a66 100%)" role="img" aria-label="Pizza baking in a stone oven"></div>
  <h3 class="script sub abs" style="left:238px;top:62px">What Sets Our Trattoria Apart</h3>
  <ul class="bullets text abs" style="left:240px;top:89px;width:250px">
    <li>At Delphine's Stone Hearth Trattoria, our commitment to excellence sets us apart. We pride ourselves on using carefully crafted proprietary recipes for our homemade sauce and dough, resulting in exceptional product quality. Our small, profitable menu ensures consistency and allows us to deliver lightning-quick food times, making us a customer favorite.</li>
  </ul>
  <h3 class="script sub abs" style="left:10px;top:181px">Key Differentiators and Competitive Advantages:</h3>
  <p class="text abs" style="left:18px;top:206px;width:246px;text-align:right">Our ability to make anything on our menu in a matter of minutes, ● coupled with our convenient ordering options, including mobile ordering, delivery service, takeout, and in-person dining, sets us apart from the competition. We prioritize meeting our customers' exact fast-paced needs and providing the best quality product and service.</p>
  <div class="photo" style="left:290px;top:175px;width:154px;height:104px;background:linear-gradient(160deg,#cfcac4 0%,#e3a55a 40%,#c9762e 65%,#6a5440 100%)" role="img" aria-label="Chef lifting a pizza on a peel"></div>
  <div class="page">Page 04</div>
</section>

<!-- Investment Opportunity -->
<section class="slide s5">
  <h2 class="script title abs" style="left:0;width:509px;text-align:center;top:2px;font-size:38px">Investment Opportunity</h2>
  <div class="rule" style="left:192px;top:42px;width:125px"></div>
  <div class="brand brand-sm" style="left:467px;top:17px">Delphine's</div>
  <div class="photo round" style="left:44px;top:57px;width:70px;height:70px;background:radial-gradient(#c8481e,#9c3517 70%,#2a1a12)" role="img" aria-label="Margherita pizza from above"></div>
  <div class="photo round" style="left:132px;top:57px;width:70px;height:70px;background:radial-gradient(#e8c07a,#d39a4f 70%,#3a2a1c)" role="img" aria-label="White pizza with tomatoes and egg"></div>
  <div class="photo round" style="left:219px;top:57px;width:70px;height:70px;background:radial-gradient(#b0643a,#7e4223 70%,#2a1a12)" role="img" aria-label="Meat lovers pizza from above"></div>
  <div class="photo round" style="left:308px;top:57px;width:70px;height:70px;background:radial-gradient(#e6cfa0,#b99966 70%,#3a2a1c)" role="img" aria-label="Dessert pizza with chocolate drizzle"></div>
  <div class="photo round" style="left:395px;top:57px;width:70px;height:70px;background:radial-gradient(#e9a75a,#d07a32 70%,#3a2a1c)" role="img" aria-label="Sausage and cheese pizza from above"></div>
  <h3 class="script sub abs" style="left:13px;top:143px">Funding Requirements and Use of Funds:</h3>
  <ul class="bullets text abs" style="left:13px;top:170px;width:467px"><li style="text-align:left">To support our expansion plans and achieve our growth targets, we are seeking an investment of $2 million. The funds will be used for new location build-outs, equipment purchases, marketing and advertising campaigns, operational reserves, and working capital.</li></ul>
  <h3 class="script sub abs" style="left:13px;top:205px">Equity or Debt Investment Options:</h3>
  <ul class="bullets text abs" style="left:13px;top:233px;width:230px"><li>We are open to both equity and debt investment options. We can discuss the terms and conditions based on the investor's preferences and our mutual goals.</li></ul>
  <h3 class="script sub abs" style="left:260px;top:205px">Proposed Investment Structure and Terms:</h3>
  <ul class="bullets text abs" style="left:261px;top:233px;width:230px"><li>The investment structure and terms will be negotiated based on the investment amount and the level of involvement desired by the investor. We are committed to ensuring a mutually beneficial partnership that aligns with our long-term growth plans.</li></ul>
  <div class="page">Page 05</div>
</section>

<!-- Conclusion -->
<section class="slide s6">
  <div class="storefront" role="img" aria-label="Faded photo of the trattoria storefront and signage"></div>
  <div class="brand" style="left:254px;top:30px;font-size:26px">Delphine's</div>
  <h2 class="script abs" style="left:0;width:509px;text-align:center;top:88px;font-size:34px">Conclusion and Contact Information</h2>
  <div class="rule" style="left:191px;top:127px;width:126px"></div>
  <h3 class="script sub abs" style="left:0;width:509px;text-align:center;top:135px;font-size:19px">Conclusion:</h3>
  <p class="text abs" style="left:12px;top:155px;width:485px;text-align:center">Delphine's Stone Hearth Trattoria presents an exciting investment opportunity in the thriving pizza industry. With our unique selling proposition, strong growth strategy, and experienced management team, we are well-positioned to expand and build out Delphine's to 50-100 locations.</p>
  <h3 class="script sub abs" style="left:0;width:509px;text-align:center;top:191px;font-size:19px">Contact Information</h3>
  <div class="rule" style="left:224px;top:213px;width:60px;height:1px"></div>
  <div class="portrait" style="left:98px;top:245px"><div class="face" role="img" aria-label="Portrait of Marco Bellanti"></div></div>
  <div class="portrait" style="left:296px;top:245px"><div class="face" role="img" aria-label="Portrait of Owen Hartley"></div></div>
  <div class="person left" style="left:139px;top:223px"><div class="name">MARCO BELLANTI</div><div class="role">Owner &amp; CEO</div><div class="dash"></div><div class="email">marco@delphinestrattoria.com</div></div>
  <div class="person left" style="left:337px;top:223px"><div class="name">OWEN HARTLEY</div><div class="role">Owner, Silent Partner</div><div class="dash"></div><div class="email">owen@delphinestrattoria.com</div></div>
</section>

</body>
</html>
```